Brightwave Exterior cleaning Logo

We need a new business card design, i would like to use our existing logo (attached).
Our logo on the left & a unique graphic design on the right of either a man holding a pressure washer gun & hose with a thumbs up or an image portraying dirt melting off a building or the two incorperated together, or something similar that represents exterior cleaning in progress, an image that shows/explains that we are exterior cleaners/pressure washers. Has to incorporate the zentrix & chatlane symbol perhaps in the bottom corners of the business card.
Existing business symbol on the back of the card with some blank lines for space to hand write quotes or job notes.
Industry/Entity Type
Exterior Cleaning
Contact Information for Business Card
Business mobile No. to be prominent (0472 918 346) Services provided listed as dot points. -Soft Washing -Pressure Washing - Solar Panel Cleaning - All General Exterior Cleaning. Email listed in fineprint (enquiries@tallowbrookwashworks.com.au). Owner Operator - Declan Morrow (this should also be added somewhere prominent). Residential & Comercial Cleaning.
Colors
Designer to choose colors to be used in the design.
Look and feel

```html
<!DOCTYPE html>
<html lang="en">
<head>
<meta charset="utf-8">
<title>Tallowbrook Washworks – Business Card</title>
<link rel="stylesheet" href="https://fonts.googleapis.com/css2?family=Roboto:wght@400;700&display=swap">
<style>
  :root {
    --bg: #3b3b3b;
    --card: #141414;
    --blue: #4a62b5;
    --white: #ffffff;
    --pattern-dark: #060606;
    --pattern-mid: #1d1d1d;
    --pattern-light: #454545;
  }
  * { box-sizing: border-box; margin: 0; padding: 0; }
  html, body {
    width: 1200px; height: 801px; overflow: hidden;
    background: var(--bg);
    font-family: "Roboto", Arial, sans-serif;
  }
  .stage {
    width: 1200px; height: 801px;
    display: flex; align-items: center; justify-content: center; gap: 40px;
  }
  .card {
    position: relative;
    width: 540px; height: 320px;
    border-radius: 16px;
    background: var(--card);
    overflow: hidden;
    box-shadow: 0 10px 30px rgba(0,0,0,.45);
  }
  /* front */
  .brand {
    position: absolute; left: 34px; top: 150px; width: 176px;
    display: flex; align-items: center; gap: 10px;
  }
  .brand-square { width: 22px; height: 22px; background: var(--blue); flex: none; }
  .brand-name {
    color: var(--white); font-weight: 700; font-size: 18px;
    line-height: 1.15; text-transform: uppercase; letter-spacing: .5px;
  }
  .divider {
    position: absolute; left: 222px; top: 48px; width: 1px; height: 180px;
    background: var(--blue);
  }
  .contact { position: absolute; left: 244px; top: 44px; right: 16px; }
  .person-name {
    color: var(--blue); font-weight: 700; font-size: 24px;
    text-transform: uppercase; letter-spacing: -.3px;
  }
  .person-role { color: var(--white); font-size: 14px; margin: 2px 0 12px; }
  .line {
    display: flex; align-items: center; gap: 7px;
    color: var(--white); font-size: 12px; margin-bottom: 5px;
    white-space: nowrap;
  }
  .line svg { width: 12px; height: 12px; flex: none; fill: var(--blue); }
  .line.phone { color: var(--blue); font-weight: 700; font-size: 16px; }
  .line.phone svg { width: 14px; height: 14px; }
  .tagline { color: var(--white); font-size: 13px; margin-top: 10px; }
  .services-band {
    position: absolute; left: 0; right: 0; bottom: 0; height: 36px;
    padding: 0 14px;
    background: var(--blue);
    display: flex; align-items: center; justify-content: center;
    color: var(--white); font-size: 12.5px; white-space: nowrap;
  }
  /* back */
  .back-pattern {
    position: absolute; inset: 0;
    background:
      radial-gradient(ellipse at 80% 85%, rgba(90,90,90,.35) 0%, rgba(90,90,90,0) 60%),
      linear-gradient(125deg, var(--pattern-dark) 0%, var(--pattern-mid) 50%, var(--pattern-light) 100%);
  }
  .back-brand {
    position: absolute; right: 48px; top: 196px;
    display: flex; align-items: center; gap: 8px;
  }
  .back-brand .brand-square { width: 18px; height: 18px; }
  .back-brand .brand-name { font-size: 13px; }
</style>
</head>
<body>
<main class="stage">
  <section class="card card-front" aria-label="Business card front">
    <div class="brand">
      <span class="brand-square"></span>
      <span class="brand-name">Tallowbrook Washworks</span>
    </div>
    <div class="divider"></div>
    <div class="contact">
      <h1 class="person-name">Declan Morrow</h1>
      <p class="person-role">Owner Operator</p>
      <p class="line phone">
        <svg viewBox="0 0 24 24"><path d="M6.6 10.8a15.1 15.1 0 0 0 6.6 6.6l2.2-2.2c.3-.3.7-.4 1-.2 1.1.4 2.3.6 3.6.6.6 0 1 .4 1 1V20c0 .6-.4 1-1 1A17 17 0 0 1 3 4c0-.6.4-1 1-1h3.5c.6 0 1 .4 1 1 0 1.3.2 2.5.6 3.6.1.3 0 .7-.2 1z"/></svg>
        0472 918 346
      </p>
      <p class="line">
        <svg viewBox="0 0 24 24"><path d="M2 5h20v14H2zm2 2v.5l8 5 8-5V7z"/></svg>
        enquiries@tallowbrookwashworks.com.au
      </p>
      <p class="line">
        <svg viewBox="0 0 24 24"><path d="M12 2a10 10 0 1 0 0 20 10 10 0 0 0 0-20zm6.9 9h-3a15 15 0 0 0-1.3-5.6A8 8 0 0 1 18.9 11zM12 4c.9 1.3 1.7 3.9 1.9 7h-3.8c.2-3.1 1-5.7 1.9-7zM9.4 5.4A15 15 0 0 0 8.1 11h-3a8 8 0 0 1 4.3-5.6zM5.1 13h3a15 15 0 0 0 1.3 5.6A8 8 0 0 1 5.1 13zM12 20c-.9-1.3-1.7-3.9-1.9-7h3.8c-.2 3.1-1 5.7-1.9 7zm2.6-1.4a15 15 0 0 0 1.3-5.6h3a8 8 0 0 1-4.3 5.6z"/></svg>
        www.tallowbrookwashworks.com.au
      </p>
      <p class="tagline">Residential &amp; Comercial Cleaning</p>
    </div>
    <div class="services-band">Soft Washing &bull; Pressure Washing &bull; Solar Panel Cleaning &bull; All General Exterior Cleaning</div>
  </section>

  <section class="card card-back" aria-label="Business card back">
    <div class="back-pattern" role="img" aria-label="Repeating pattern of diamond tiles shading from black at top left to grey at bottom right"></div>
    <div class="back-brand">
      <span class="brand-square"></span>
      <span class="brand-name">Tallowbrook Washworks</span>
    </div>
  </section>
</main>
</body>
</html>
```